Coffee House With Cycling Theme Wants Business Cards

We want to create a business card for a coffee house that has a cycling theme. We expect to use the current logo on one side of the business card and we have been considering adding the words 'COFFEE HOUSE' underneath (see example). For the other side of the business card we want an interesting design with tag-line, address and social media links (the normal business card stuff). See examples provided but we are not fixed on having it exactly as shown, we are very open to great creative ideas. Please note our logo has the initials ‘KR' in orange embedded in the design and this must be retained. However, you can play with the words COFFEE HOUSE as well as use the orange color on the backside of the business card, as you see fit. For an image on the backside of the business card it can be a photo, hand-drawn or whatever but it must visually combine coffee and cycling in some way. The interior of the Coffee House will be reclaimed wood, rustic and have an urban feel to it with cycling artifacts hanging from the walls/ceiling, etc. Finally, it would be beneficial if the business card design elements can be easily used on flyers and other promotional assets. Good luck, we are looking forward to seeing your creative ideas.

Target Market(s)

Coffee lovers and cycling fans

Contact Information for Business Card

See project description.

Colors

Designer to choose colors to be used in the design.

Requirements
Must have
• Must use the current logo provided and combine a coffee and bike theme.
Nice to have
• Orange is used in current logo and could be used as an accent color on the backside of the business card.

```html
<!DOCTYPE html>
<html lang="en">
<head>
<meta charset="utf-8">
<title>KR Coffee House – Business Cards</title>
<link rel="stylesheet" href="https://fonts.googleapis.com/css2?family=Open+Sans:wght@400;600&family=Roboto:wght@400;500&display=swap">
<style>
  :root {
    --orange: #f26a2e;
    --orange-light: #f47a44;
    --ink: #2a2a2a;
    --paper: #ffffff;
    --backdrop: #9a9a9a;
  }
  html, body {
    margin: 0;
    padding: 0;
    width: 1200px;
    height: 930px;
    overflow: hidden;
    background: var(--backdrop);
  }
  .canvas {
    position: relative;
    width: 1200px;
    height: 930px;
  }
  .card {
    position: absolute;
    width: 540px;
    height: 320px;
    border-radius: 22px;
    overflow: hidden;
    box-shadow: 0 6px 18px rgba(0,0,0,0.25);
  }
  /* Front */
  .card--front {
    left: 80px;
    top: 140px;
    background: linear-gradient(135deg, var(--orange-light), var(--orange));
    display: flex;
    align-items: center;
    justify-content: center;
  }
  .brand {
    font-family: "Open Sans", sans-serif;
    font-weight: 400;
    letter-spacing: 2px;
    white-space: nowrap;
  }
  .card--front .brand {
    color: var(--paper);
    font-size: 44px;
  }
  /* Back */
  .card--back {
    left: 580px;
    top: 480px;
    background: var(--paper);
  }
  .card--back .brand {
    position: absolute;
    left: 34px;
    top: 56px;
    color: var(--ink);
    font-size: 28px;
  }
  .person {
    position: absolute;
    right: 34px;
    top: 42px;
    text-align: right;
    font-family: "Roboto", sans-serif;
  }
  .person__name {
    color: var(--orange);
    font-weight: 500;
    font-size: 22px;
    letter-spacing: 1px;
    margin: 0;
  }
  .person__role {
    color: var(--ink);
    font-size: 13px;
    margin: 2px 0 0;
  }
  .band {
    position: absolute;
    left: 0;
    right: 0;
    top: 130px;
    height: 130px;
    background: var(--orange);
    color: var(--paper);
    font-family: "Roboto", sans-serif;
  }
  .contact-list {
    position: absolute;
    left: 34px;
    bottom: 16px;
    margin: 0;
    padding: 0;
    list-style: none;
    font-size: 14px;
    line-height: 22px;
  }
  .contact-list li {
    display: flex;
    align-items: center;
    gap: 8px;
  }
  .contact-list svg { width: 11px; height: 11px; }
  .address {
    position: absolute;
    right: 34px;
    top: 22px;
    margin: 0;
    text-align: right;
    font-size: 14px;
    line-height: 20px;
    font-style: normal;
  }
  .social {
    position: absolute;
    left: 0;
    right: 0;
    bottom: 20px;
    display: flex;
    justify-content: center;
    gap: 36px;
    font-family: "Roboto", sans-serif;
    font-size: 15px;
    color: var(--ink);
  }
  .social__item {
    display: flex;
    align-items: center;
    gap: 8px;
  }
  .social__mark {
    width: 16px;
    height: 16px;
    background: var(--orange);
  }
  .social__mark--round { border-radius: 50%; }
</style>
</head>
<body>
<main class="canvas">
  <section class="card card--front" aria-label="Card front">
    <span class="brand">KR COFFEE HOUSE</span>
  </section>

  <section class="card card--back" aria-label="Card back">
    <span class="brand">KR COFFEE HOUSE</span>

    <div class="person">
      <p class="person__name">DANIEL HART</p>
      <p class="person__role">Director</p>
    </div>

    <div class="band">
      <address class="address">42b Harbour Lane,<br>Riverton, NZ, 9012</address>
      <ul class="contact-list">
        <li>
          <svg viewBox="0 0 12 12" aria-hidden="true"><path d="M2 1l2 0 1 3-1.5 1a6 6 0 0 0 3.5 3.5L8 7l3 1v2c0 .6-.4 1-1 1A9 9 0 0 1 1 2c0-.6.4-1 1-1z" fill="#fff"/></svg>
          (555) 010-4782
        </li>
        <li>
          <svg viewBox="0 0 12 12" aria-hidden="true"><rect x="1" y="2.5" width="10" height="7" fill="none" stroke="#fff" stroke-width="1.2"/><path d="M1 3l5 3.5L11 3" fill="none" stroke="#fff" stroke-width="1.2"/></svg>
          info@krcoffeehouse.com
        </li>
        <li>
          <svg viewBox="0 0 12 12" aria-hidden="true"><circle cx="6" cy="6" r="5" fill="none" stroke="#fff" stroke-width="1.2"/><path d="M1 6h10M6 1c-2.5 3-2.5 7 0 10M6 1c2.5 3 2.5 7 0 10" fill="none" stroke="#fff" stroke-width="1"/></svg>
          www.krcoffeehouse.com
        </li>
      </ul>
    </div>

    <div class="social">
      <span class="social__item"><span class="social__mark"></span>krcoffeehouse.com</span>
      <span class="social__item"><span class="social__mark social__mark--round"></span>krcoffeehouse.com</span>
    </div>
  </section>
</main>
</body>
</html>
```